ONE PAGE WEB DESIGN NEEDED for Finance Company

We need a web design (ONE PAGE DESIGN ONLY) for a new finance website called Tidewell Lending. Tidewell Lending helps customers get the right loan, whether its a home loan, investment loan, business loan etc.

You are required to come up with just the homepage design. Professionalism and quality is the key factors in the successful design.

Here are a few design questions to help you out:

-
What information should be used on the page?
Ive provided a document which outlines all the information needed to put on homepage (attached to the brief - called tidewell_page_info). Also see the Must Have section below on this brief.

-
What links should appear in the navigation/footer?:
The navigation should provide links to the following pages (NOTE: services link has subcategories):
1 Homepage
2 Services
- Home loans
- Investment loans
- Refinancing loans
- Business loans
3 About Us
4 FAQ
5 Contact Us

-
What colors should be used in the design?
Our company colors - Cyan: #2EADE3, Blue: #004B70, White. Feel free to submit designs with slight variations if you feel it improves the design.

-
What should the layout of the page be?
This is up to you to come up with - we are open to different layouts for the page design (as long as they capture the information effectively and making it easy to understand).

Target Market(s)

Potential Home owners, Families and Business Owners

Industry/Entity Type

Business

Requirements
Must have
• - Must contain our logo (attached as PNG and Illustrator file)
- Winning designer must supply a Photoshop file (PSD) that will allow us.
Nice to have
• - Should include photos/images of families, professional groups, tradespeople etc (you can use stock photos from PixaVault and I will purchase them once you are selected as the winning design)
- Link to a loan calculator somewhere on front page with a button 'Find out how much you could borrow' (or maybe even try adding a loan calculator to the homepage if you think this would look good)
- Page should have a main headline "Finding the right loan for you" or "Tidewell Lending finds the right loan for our customers."
- Must include Accreditation logos somewhere on the homepage (will try and supply these soon)
Should not have
• - Poor quality designs will not be considered
- Do not use clipart

```html
<!DOCTYPE html>
<html lang="en">
<head>
<meta charset="utf-8">
<title>Tidewell Lending – Home</title>
<link rel="stylesheet" href="https://fonts.googleapis.com/css2?family=Questrial&family=Tinos:ital,wght@0,400;0,700;1,700&family=Arimo:wght@400;700&display=swap">
<style>
:root{
  --cyan:#2eade3;
  --cyan-light:#5fc4ec;
  --blue:#004b70;
  --blue-mid:#1a7fb5;
  --ink:#333333;
  --muted:#666666;
  --orange:#e8620c;
  --link:#0a6fa0;
  --rule:#d9d9d9;
  --yellow:#ffe53b;
}
*{box-sizing:border-box;margin:0;padding:0}
html,body{width:1200px;height:1086px;overflow:hidden;background:#fff}
body{position:relative;font-family:"Tinos",serif;color:var(--ink)}
.abs{position:absolute}

.top-band{position:absolute;left:0;top:0;width:1200px;height:60px}
.phone-line{position:absolute;right:153px;top:15px;font-family:"Questrial",sans-serif;font-size:18px;color:#fff}
.phone-line strong{color:var(--yellow);font-weight:700;font-family:"Arimo",sans-serif;font-size:17px}

.brand{position:absolute;left:146px;top:92px;display:flex;align-items:center;gap:8px}
.brand-dot{width:14px;height:14px;border-radius:50%;background:var(--cyan)}
.brand-name{font-family:"Arimo",sans-serif;font-weight:700;font-size:25px;color:var(--cyan);letter-spacing:-0.5px}

.main-nav{position:absolute;left:503px;top:57px;display:flex;height:64px;font-family:"Arimo",sans-serif;font-weight:700;font-size:13px}
.main-nav a{display:flex;align-items:center;text-decoration:none;color:#0d2a3a;padding:0 25px;height:64px}
.main-nav a.current{background:#f0f0f0;color:var(--cyan);border-bottom:2px solid var(--cyan);position:relative;width:98px;justify-content:center;padding:0}
.main-nav a.current::after{content:"";position:absolute;bottom:-7px;left:45px;border:5px solid transparent;border-top-color:var(--cyan)}
.main-nav a.services{padding-left:24px}

.hero{position:absolute;left:153px;top:154px;width:894px;height:334px;border:1px solid #cfcfcf;padding:6px;background:#fff}
.hero-media{width:100%;height:100%;background:linear-gradient(100deg,#8fbfe3 0%,#c9a989 28%,#e7d2bf 48%,#eeeeee 66%,#f3f3f3 100%);position:relative}
.hero-team{position:absolute;right:12px;bottom:0;width:310px;height:215px;border-radius:155px 155px 0 0;background:linear-gradient(180deg,#f7f7f7,#d6dde6)}
.hero-title{position:absolute;right:24px;top:22px;text-align:right}
.hero-title h1{font-family:"Questrial",sans-serif;font-weight:400;font-size:38px;color:#1f6f9c;letter-spacing:0.5px;line-height:1}
.hero-title p{font-family:"Questrial",sans-serif;font-size:21px;color:#333;margin-top:7px}

.intro{position:absolute;left:153px;top:512px;width:630px;font-size:14px;line-height:24px;color:#444}
.intro .lead{font-size:34px;color:var(--cyan);line-height:34px}

.calc-cta{position:absolute;left:796px;top:519px;width:251px;height:124px;background:linear-gradient(135deg,#0f8fd0,#3cb7ea);overflow:hidden}
.calc-art{position:absolute;right:0;top:0;width:110px;height:124px;background:linear-gradient(180deg,rgba(255,255,255,0.05),rgba(240,220,160,0.55))}
.calc-cta .kicker{position:absolute;left:13px;top:9px;font-style:italic;font-weight:700;font-size:25px;color:var(--yellow);letter-spacing:0.5px}
.calc-cta .sub{position:absolute;left:13px;top:37px;font-style:italic;font-weight:700;font-size:20px;line-height:22px;color:#fff}
.calc-cta .btn{position:absolute;left:13px;top:86px;padding:4px 9px;background:#fff36a;border-radius:4px;font-family:"Arimo",sans-serif;font-weight:700;font-size:13px;color:#0d3048}

.offer-heading{position:absolute;left:153px;top:690px;font-family:"Questrial",sans-serif;font-size:19px;color:var(--orange)}

.loan-cards{position:absolute;left:153px;top:729px;display:flex;gap:2px}
.loan-card{width:222px;height:192px;position:relative;border-right:1px solid #ececec;box-shadow:2px 0 6px -4px rgba(0,0,0,0.12)}
.loan-card h2{height:45px;padding:12px 0 0 23px;font-family:"Questrial",sans-serif;font-weight:400;font-size:18px;color:#222;letter-spacing:0.5px;border-bottom:4px solid}
.loan-card.home h2{background:#e6e6e6;border-color:#c9c9c9}
.loan-card.invest h2{background:#b8e3f3;border-color:#5cc3e6}
.loan-card.refi h2{background:#cff1f9;border-color:#74d3ec}
.loan-card.business h2{background:#bcdcf8;border-color:#7cb9ec}
.loan-card ul{list-style:none;padding:13px 0 0 25px;font-size:14px;line-height:26px;color:#333}
.loan-card li{position:relative;padding-left:16px}
.loan-card li::before{content:"";position:absolute;left:0;top:9px;width:6px;height:6px;border-radius:50%;border:1px solid #aaa;background:#e3e3e3}
.loan-card li.wrap{line-height:21px;padding-top:3px}
.loan-card .more{position:absolute;left:25px;bottom:8px;font-size:12px;color:var(--link);text-decoration:none}

.partners{position:absolute;left:242px;top:960px;display:flex;align-items:center;gap:12px}
.partners .label{font-size:12px;font-weight:700;color:#111;margin-right:2px}
.partner-badge{height:18px;border-radius:2px}

.footer-rule{position:absolute;left:0;top:999px;width:1200px;height:3px;background:linear-gradient(#f2f2f2,#e2e2e2)}
.footer-nav{position:absolute;left:153px;top:1021px;font-family:"Arimo",sans-serif;font-size:12px;color:#444;display:flex;gap:0}
.footer-nav a{color:#444;text-decoration:none}
.footer-nav span{margin:0 15px}
.copyright{position:absolute;left:153px;top:1043px;font-family:"Arimo",sans-serif;font-size:10.5px;color:#777}
.accreditations{position:absolute;left:846px;top:1021px;display:flex;gap:18px;align-items:center}
.accred{width:26px;height:32px;background:#111}
.accred.wide{width:42px;height:22px;background:#555;border-radius:2px}
.accred.ring{width:54px;height:24px;border:2px solid #444;border-radius:12px;background:none}
.accred.square{width:34px;height:32px;background:#111}
.bottom-band{position:absolute;left:0;top:1078px;width:1200px;height:8px;background:var(--blue-mid)}
</style>
</head>
<body>

<svg class="top-band" width="1200" height="60" viewBox="0 0 1200 60" aria-hidden="true">
  <defs>
    <linearGradient id="bandFill" x1="0" y1="0" x2="0" y2="1">
      <stop offset="0" stop-color="#49b6e6"/>
      <stop offset="1" stop-color="#2a9fd8"/>
    </linearGradient>
  </defs>
  <rect x="0" y="0" width="1200" height="53" fill="url(#bandFill)"/>
  <rect x="0" y="53" width="1200" height="4" fill="#1a7fb5"/>
  <path d="M150 58 C165 -6 330 -6 345 58 Z" fill="#fff"/>
  <path d="M150 56 C165 -6 330 -6 345 56" fill="none" stroke="#1a7fb5" stroke-width="4"/>
</svg>

<p class="phone-line">Contact Tidewell Lending today on: <strong>1800 555 214</strong> to find out more</p>

<div class="brand">
  <span class="brand-dot"></span>
  <span class="brand-name">Tidewell Lending</span>
</div>

<nav class="main-nav">
  <a class="current" href="#">HOME</a>
  <a class="services" href="#">SERVICES</a>
  <a href="#">ABOUT US</a>
  <a href="#">FAQ</a>
  <a href="#">CONTACT US</a>
</nav>

<section class="hero">
  <div class="hero-media" role="img" aria-label="PixaVault stock photo of a smiling family lying on a lawn in front of a red-roofed house, with a circular inset of a professional team in business clothes">
    <div class="hero-team"></div>
    <div class="hero-title">
      <h1>TIDEWELL LENDING</h1>
      <p>finds the right loan for our customers</p>
    </div>
  </div>
</section>

<p class="intro"><span class="lead">At Tidewell Lending</span> we work hard to find the right loan for our customers. We do that because we are backed by sound industry knowledge, professional experience and a great customer service approach. Tidewell Lending guarantees that we will always tailor the best solution for your individual lending needs. We can do that because we have access to a wide variety of lending options from major banks to non-bank lenders and we are committed to finding the right lending product for you.</p>

<a class="calc-cta" href="#">
  <div class="calc-art" role="img" aria-label="Illustration of a small house resting on stacks of banknotes"></div>
  <span class="kicker">FIND OUT</span>
  <span class="sub">how much you<br>could borrow</span>
  <span class="btn">FIND IT NOW!</span>
</a>

<h2 class="offer-heading">We offer a unique approach to help you find the right Option &gt;&gt;</h2>

<section class="loan-cards">
  <article class="loan-card home">
    <h2>HOME LOAN</h2>
    <ul><li>Home buyers</li><li>First home buyers</li><li>Over 20 lenders</li></ul>
    <a class="more" href="#">| Know more...</a>
  </article>
  <article class="loan-card invest">
    <h2>INVESTMENT LOAN</h2>
    <ul><li>Property investment loans</li><li>Interest only loans</li></ul>
    <a class="more" href="#">| Know more...</a>
  </article>
  <article class="loan-card refi">
    <h2>REFINANCING</h2>
    <ul><li>Refinancing for the best rate</li><li>Upsizing or downsizing</li><li class="wrap">Change from a variable to a fixed rate</li></ul>
    <a class="more" href="#">| Know more...</a>
  </article>
  <article class="loan-card business">
    <h2>BUSINESS LOAN</h2>
    <ul><li>Long term</li><li>Short term</li><li>Equipment and Leasing</li></ul>
    <a class="more" href="#">| Know more...</a>
  </article>
</section>

<div class="partners">
  <span class="label">Our Loan Partners :</span>
  <span class="partner-badge" style="width:78px;background:#b5472a"></span>
  <span class="partner-badge" style="width:72px;background:#1f3f7a"></span>
  <span class="partner-badge" style="width:68px;background:#ff7a1a"></span>
  <span class="partner-badge" style="width:92px;background:#1c5aa0"></span>
  <span class="partner-badge" style="width:76px;background:#f26522"></span>
  <span class="partner-badge" style="width:60px;background:#e32726"></span>
  <span class="partner-badge" style="width:62px;background:#2a8ecf"></span>
</div>

<div class="footer-rule"></div>
<nav class="footer-nav">
  <a href="#">Homepage</a><span>|</span><a href="#">Services</a><span>|</span><a href="#">About Us</a><span>|</span><a href="#">FAQ</a><span>|</span><a href="#">Contact Us</a>
</nav>
<p class="copyright">Copyright©2012 www.tidewelllending.com &nbsp; All rights reserved</p>
<div class="accreditations">
  <span class="accred"></span>
  <span class="accred wide"></span>
  <span class="accred ring"></span>
  <span class="accred square"></span>
</div>
<div class="bottom-band"></div>

</body>
</html>
```